Hybrid Seed corn and Soybean Sales business needs a website.

We here at "KW Grain" feel that we need a website to show a very professional side to our customer base. Although no actual ordering will take place on this website, we would like to put Plot and field trail data on the website. Along with a brief page for each of our hybrids and a place for customers to sign up for a newsletter. The company we sell hybrids for is MolvanGrain.com... Im not sure how this process works as far as myself updating the information or having the data actually put on the website, but feel free to contact me if you need the information. I will attach the logo for the company, (KW Grain).

Target Market(s)

Farmers, "Producers", Corn and soybean production

Industry/Entity Type

Business

Coding

Coded - Design and coding required

Number of Pages Required

5+ page

Colors
f78f20
ffffff

Requirements
Nice to have
• Similar layout to http://www.molvangrain.com/
• And it would be nice to incorporate our story into the website
• http://www.molvangrain.com/our-story/molvan-today/

```html
<!DOCTYPE html>
<html lang="en">
<head>
<meta charset="utf-8">
<title>KW Grain – Hybrid Seed Corn &amp; Soybeans</title>
<link href="https://fonts.googleapis.com/css2?family=Raleway:wght@400;500;600;700&family=Open+Sans:wght@400;600&display=swap" rel="stylesheet">
<style>
:root{
  --orange:#f78f20;
  --orange-deep:#f26a10;
  --orange-dark:#e0621b;
  --ink:#222;
  --muted:#555;
  --green:#5c9e24;
  --line:#d8d8d8;
  --white:#fff;
}
*{box-sizing:border-box;margin:0;padding:0}
html,body{width:889px;height:1200px;overflow:hidden}
body{position:relative;background:var(--white);font-family:"Open Sans",Arial,sans-serif;color:var(--ink)}
.abs{position:absolute}

.site-header{top:0;left:0;width:889px;height:81px}
.brand{left:140px;top:28px;display:flex;align-items:center;gap:8px;font-family:"Raleway",Arial,sans-serif;font-weight:700;font-size:22px;color:var(--orange-deep)}
.brand-mark{width:30px;height:30px;border-radius:50%;background:var(--green)}
.call{right:143px;top:35px;text-align:right;font-family:"Raleway",Arial,sans-serif}
.call-label{font-size:11px;color:var(--orange-deep);letter-spacing:.2px}
.call-number{font-size:15px;color:var(--ink);display:flex;align-items:center;gap:3px;justify-content:flex-end;margin-top:1px}

.main-nav{top:81px;left:0;width:889px;height:35px;background:linear-gradient(var(--orange) 0%,var(--orange-deep) 100%)}
.main-nav ul{list-style:none;display:flex;position:absolute;left:146px;top:0;height:35px}
.main-nav li{font-family:"Raleway",Arial,sans-serif;font-size:11px;font-weight:500;color:var(--white);height:35px;line-height:35px;padding:0 17px;border-right:1px solid rgba(255,255,255,.35)}
.main-nav li:last-child{border-right:0}

.hero{top:116px;left:0;width:889px;height:327px;background:linear-gradient(180deg,#b9cfc9 0%,#c7b79b 14%,#a88659 26%,#8e8a4a 33%,#5f9a2a 42%,#4e9a1e 70%,#3f8a17 100%)}
.hero-caption{left:134px;top:203px;width:312px;height:118px;background:rgba(88,150,30,.88);padding:18px 20px;color:var(--white);font-family:"Raleway",Arial,sans-serif}
.hero-kicker{font-size:15px;font-weight:500}
.hero-title{font-size:27px;font-weight:600;line-height:1.1;margin-top:2px}
.hero-text{font-family:"Open Sans",Arial,sans-serif;font-size:8px;line-height:13px;margin-top:8px;padding-left:4px}
.slider-dots{left:415px;top:421px;display:flex;gap:4px}
.slider-dots span{width:11px;height:11px;border-radius:50%;background:var(--white)}
.slider-dots span.active{background:#111}

.feature{top:461px;width:196px;height:191px;border:1px solid var(--line);background:linear-gradient(#fff 60%,#efefef 100%);text-align:center;box-shadow:0 6px 6px -5px rgba(0,0,0,.18)}
.feature-icon{width:52px;height:52px;margin:20px auto 0;border-radius:12px;background:#fbd2a6}
.feature-title{font-family:"Raleway",Arial,sans-serif;font-size:14px;font-weight:500;margin-top:24px}
.feature-text{font-size:7.3px;line-height:13px;color:var(--muted);margin:8px 24px 0}

.about{left:140px;top:713px;width:355px}
.about h2{font-family:"Raleway",Arial,sans-serif;font-weight:500;font-size:20px}
.about p{font-size:7.3px;line-height:13px;color:#444;margin-top:8px}
.btn-more{display:inline-block;margin-top:10px;background:linear-gradient(var(--orange),var(--orange-deep));color:var(--white);font-family:"Raleway",Arial,sans-serif;font-size:7.5px;padding:5px 12px;border-radius:2px}
.video{left:510px;top:717px;width:236px;height:141px;background:radial-gradient(circle at 55% 85%,#ffd15a 0%,#e07a1c 18%,#7a3514 45%,#2a140c 100%)}
.play{left:102px;top:55px}

.partners{top:926px;left:0;width:889px;height:79px;background:linear-gradient(#fff,#ececec);border-top:1px solid #ddd}
.partners-label{left:147px;top:30px;font-family:"Raleway",Arial,sans-serif;font-size:15px;color:#777}
.partner{top:31px;font-family:"Raleway",Arial,sans-serif;font-weight:700;font-size:14px;color:#555;display:flex;align-items:center;gap:5px}
.partner i{width:10px;height:10px;background:#999;display:inline-block}

.site-footer{top:1005px;left:0;width:889px;height:152px;background:linear-gradient(var(--orange) 0%,#f5882a 100%)}
.footer-col{top:34px;font-family:"Raleway",Arial,sans-serif;color:var(--white)}
.footer-col h3{font-size:11px;font-weight:500;letter-spacing:.2px;margin-bottom:4px}
.footer-col li{list-style:none;font-size:8.5px;line-height:15.6px}
.footer-divider{top:36px;width:1px;height:90px;background:rgba(255,255,255,.3)}
.newsletter p{font-size:7px;margin-bottom:5px}
.field{width:125px;height:17px;background:#fff;font-family:"Open Sans",Arial,sans-serif;font-size:6.5px;color:#333;padding:4px 7px;margin-bottom:4px;border:1px solid #ddd}
.signup-btn{width:70px;height:19px;background:#6aa524;margin-top:1px}

.footer-bar{top:1157px;left:0;width:889px;height:43px;background:var(--orange-dark)}
.copyright{left:160px;top:16px;font-size:7.5px;color:rgba(255,255,255,.85)}
.social{right:145px;top:14px;display:flex;gap:7px}
.social span{width:12px;height:12px;border-radius:50%;background:var(--white)}
</style>
</head>
<body>

<header class="site-header abs">
  <div class="brand abs"><span class="brand-mark"></span>KW Grain</div>
  <div class="call abs">
    <div class="call-label">CALL US NOW</div>
    <div class="call-number">
      <svg width="13" height="13" viewBox="0 0 24 24" aria-hidden="true"><path fill="#f26a10" d="M6.6 10.8a15.1 15.1 0 0 0 6.6 6.6l2.2-2.2c.3-.3.7-.4 1-.2 1.1.4 2.3.6 3.6.6.6 0 1 .4 1 1V20c0 .6-.4 1-1 1A17 17 0 0 1 3 4c0-.6.4-1 1-1h3.5c.6 0 1 .4 1 1 0 1.3.2 2.5.6 3.6.1.3 0 .7-.2 1z"/></svg>
      (07) 5550 1827
    </div>
  </div>
</header>

<nav class="main-nav abs">
  <ul>
    <li>HOME</li><li>ABOUT US</li><li>SERVICES</li><li>OUR SEEDS</li><li>PRODUCTS</li><li>RESOURCES</li><li>CONTACT</li>
  </ul>
</nav>

<section class="hero abs" role="img" aria-label="Photo of green crop rows stretching toward brown hills">
  <div class="hero-caption abs" style="top:87px">
    <div class="hero-kicker">Proin nulla arcu nonummy luctus</div>
    <div class="hero-title">We Sell Hybrid seeds</div>
    <div class="hero-text">Lorem ipsum dolor sit amet consectetuer adipiscing elit Nam cursus Morbi ut mi Nullam enim leo egestas</div>
  </div>
  <div class="slider-dots abs" style="top:305px"><span class="active"></span><span></span><span></span><span></span></div>
</section>

<article class="feature abs" style="left:135px">
  <div class="feature-icon" role="img" aria-label="Icon of a seedling held in a hand"></div>
  <h3 class="feature-title">Seeds You Need</h3>
  <p class="feature-text">ue eu imperdiet ac nisl Cum sociis natoque penatibus et magnis dis parturient montes nascetur ridiculus mus In iaculis facilisis massa Etiam eu urna Sed porta</p>
</article>
<article class="feature abs" style="left:343px">
  <div class="feature-icon" role="img" aria-label="Icon of two seed kernels"></div>
  <h3 class="feature-title">Corn Seeds</h3>
  <p class="feature-text">ue eu imperdiet ac nisl Cum sociis natoque penatibus et magnis dis parturient montes nascetur ridiculus mus In iaculis facilisis massa Etiam eu urna Sed porta</p>
</article>
<article class="feature abs" style="left:552px">
  <div class="feature-icon" role="img" aria-label="Icon of a seed bag"></div>
  <h3 class="feature-title">Soybean Seeds</h3>
  <p class="feature-text">ue eu imperdiet ac nisl Cum sociis natoque penatibus et magnis dis parturient montes nascetur ridiculus mus In iaculis facilisis massa Etiam eu urna Sed porta</p>
</article>

<section class="about abs">
  <h2>About Our Company</h2>
  <p>Pellentesque faucibus Ut accumsan ultricies elit Maecenas at justo id velit placerat molestie Donec dictum lectus non odio Cras a ante vitae enim iaculis aliquam Mauris nunc quam venenatis nec euismod sit amet egestas placerat est Pellentesque habitant morbi tristique senectus et netus et malesuada fames ac turpis egestas Cras id elit Integer quis urna Ut ante enim dapibus</p>
  <p>Malesuada fringilla eu condimentum quis tellus Aenean porttitor eros vel dolor Donec convallis pede venenatis nibh Duis quam Nam eget lacus Aliquam erat volutpat Quisque dignissim congue leo</p>
  <span class="btn-more">READ MORE</span>
</section>

<div class="video abs" role="img" aria-label="Video still of a sunset over a field">
  <svg class="play abs" width="32" height="32" viewBox="0 0 32 32" aria-hidden="true"><circle cx="16" cy="16" r="16" fill="#fff"/><path d="M12 9l11 7-11 7z" fill="#111"/></svg>
</div>

<section class="partners abs">
  <div class="partners-label abs">Our Partners</div>
  <div class="partner abs" style="left:272px"><i></i>Fieldline</div>
  <div class="partner abs" style="left:400px"><i></i>Molvan</div>
  <div class="partner abs" style="left:508px"><i></i>Harlow</div>
  <div class="partner abs" style="left:604px;font-size:11px;top:33px">Harlow Crop Sciences</div>
</section>

<footer class="site-footer abs">
  <div class="footer-col abs" style="left:160px">
    <h3>COMPANY</h3>
    <ul><li>About Us</li><li>Our Seeds</li><li>Why Choose Us</li><li>Products</li></ul>
  </div>
  <div class="footer-divider abs" style="left:284px"></div>
  <div class="footer-col abs" style="left:317px;top:31px">
    <h3>SERVICES</h3>
    <ul><li>Curabitur vel mi sit</li><li>Amet magna</li><li>Malesuada ultrices</li><li>Erat fermentum</li></ul>
  </div>
  <div class="footer-divider abs" style="left:420px"></div>
  <div class="footer-col abs" style="left:457px">
    <h3>SUPPORT</h3>
    <ul><li>Partners</li><li>Privacy Policy</li><li>Term of Use</li><li>Contact</li></ul>
  </div>
  <div class="footer-divider abs" style="left:554px"></div>
  <div class="footer-col newsletter abs" style="left:585px">
    <h3>NEWSLETTER SIGN UP</h3>
    <p>Please sign up here for latest news.</p>
    <div class="field">Your name</div>
    <div class="field">Email address</div>
    <div class="signup-btn"></div>
  </div>
</footer>

<div class="footer-bar abs">
  <div class="copyright abs">© 2015 Company Name  All right reserved  Term of Use</div>
  <div class="social abs"><span></span><span></span><span></span><span></span></div>
</div>

</body>
</html>
```